Harborline Renewal Business Card Design

Professional and clean design. The design colors should flow with the logo. Two-sided card with the website on the back which is:

www.HarborlineRenewal.example.

"Specializing in Water Damage Restoration"

On the front I need the name, email, phone, and logo.

Name: Darnell Quisby
Email: Darnell@HarborlineRenewal.example
Phone: 555-318-2046 for now

I only have the Preview and Thumbnail right now but should have the source files uploaded within a day or two.

Target Market(s)

Flood victims, home owners with water damage from busted pipes etc...

Industry/Entity Type

Business

Contact Information for Business Card

Name: Darnell Quisby

Font styles to use
Serif
Sans Serif

Requirements
Must have
• Business Card Details Info

```html
<!DOCTYPE html>
<html lang="en">
<head>
<meta charset="utf-8">
<title>Harborline Renewal — Business Card</title>
<link rel="stylesheet" href="https://fonts.googleapis.com/css2?family=Cinzel:wght@500&family=Roboto:wght@400;500&display=swap">
<style>
  :root {
    --brand-blue: #2f9bd8;
    --brand-blue-deep: #1f8acb;
    --card-white: #ffffff;
    --text-grey: #555b61;
    --stage: #e9ecef;
  }
  * { box-sizing: border-box; margin: 0; padding: 0; }
  html, body { width: 1200px; height: 950px; overflow: hidden; }
  body {
    background: var(--stage);
    font-family: "Roboto", Arial, sans-serif;
    position: relative;
  }
  .card {
    position: absolute;
    left: 250px;
    width: 700px;
    height: 400px;
    border-radius: 4px;
    box-shadow: 0 6px 18px rgba(0,0,0,0.15);
    overflow: hidden;
  }
  .card-back { top: 45px; background: var(--brand-blue); color: var(--card-white); }
  .card-front { top: 505px; background: var(--card-white); }

  .brand { display: flex; flex-direction: column; align-items: center; }
  .brand-dot { width: 58px; height: 58px; border-radius: 50%; }
  .brand-name {
    font-family: "Cinzel", Georgia, serif;
    font-weight: 500;
    font-size: 40px;
    letter-spacing: 1px;
    line-height: 1.1;
    margin-top: 10px;
    white-space: nowrap;
  }

  .card-back .brand { position: absolute; left: 0; right: 0; top: 92px; }
  .card-back .brand-dot { background: var(--card-white); }
  .tagline {
    position: absolute; left: 0; right: 0; top: 262px;
    text-align: center; font-size: 19px; letter-spacing: 0.3px;
  }

  .card-front .brand { position: absolute; left: 60px; top: 70px; }
  .card-front .brand-dot { background: var(--brand-blue); }
  .card-front .brand-name { color: var(--brand-blue); font-size: 36px; }

  .holder-name {
    position: absolute; left: 60px; bottom: 62px;
    font-size: 25px; font-weight: 500; color: var(--brand-blue-deep);
  }
  .contact-list {
    position: absolute; left: 390px; top: 215px;
    list-style: none; font-size: 16px; color: var(--text-grey);
  }
  .contact-list li { display: flex; align-items: center; gap: 8px; margin-bottom: 9px; white-space: nowrap; }
  .contact-list svg { width: 16px; height: 16px; fill: var(--brand-blue); flex: none; }
</style>
</head>
<body>
  <section class="card card-back">
    <div class="brand">
      <span class="brand-dot"></span>
      <span class="brand-name">Harborline Renewal</span>
    </div>
    <p class="tagline">Specializing in Water Damage Restoration</p>
  </section>

  <section class="card card-front">
    <div class="brand">
      <span class="brand-dot"></span>
      <span class="brand-name">Harborline Renewal</span>
    </div>
    <ul class="contact-list">
      <li>
        <svg viewBox="0 0 16 16" aria-hidden="true"><path d="M3.5 1.5l2.5 0 1 3.5-1.7 1.2a9 9 0 0 0 4.5 4.5l1.2-1.7 3.5 1v2.5c0 .8-.7 1.5-1.5 1.5A12.5 12.5 0 0 1 2 3c0-.8.7-1.5 1.5-1.5z"/></svg>
        555-318-2046 for now
      </li>
      <li>
        <svg viewBox="0 0 16 16" aria-hidden="true"><path d="M1 3.5h14v9H1z M1.5 4l6.5 5 6.5-5" fill="none" stroke="#2f9bd8" stroke-width="1.5"/><path d="M1 3.5h14L8 9z"/></svg>
        Darnell@HarborlineRenewal.example
      </li>
      <li>
        <svg viewBox="0 0 16 16" aria-hidden="true"><circle cx="8" cy="8" r="6.5" fill="none" stroke="#2f9bd8" stroke-width="1.6"/><path d="M1.5 8h13M8 1.5c-3 3.5-3 9.5 0 13M8 1.5c3 3.5 3 9.5 0 13" fill="none" stroke="#2f9bd8" stroke-width="1.2"/></svg>
        HarborlineRenewal.example
      </li>
    </ul>
    <p class="holder-name">Darnell Quisby</p>
  </section>
</body>
</html>
```